4 Poster Designs required for Nail Salon

We require 4 poster designs that will be displayed inside a shopping centre. Each design should contain our logo and the words "Located next to Tallmart" (or similar). Design 1 (MOTHERS DAY) should contain the words "Mothers Day Special" and "$10 gift voucher when you spend over $50". Design 2 (CHRISTMAS) should contain the words "Christmas in July" and "Purchase a set of nails and get a $10 gift voucher". Design 3 (ALL YEAR) should contain the words "New Deluxe Spa Pedicure Service" and the words "Try our new Deluxe Spa Pedicure and get a free nail buff, shape and polish for your fingernails". Design 4 (ALL YEAR 2)should contain high quality nail salon image(s) and the words "Now Open". We like designs that support our image of high quality/fun/clean and safe.
Updates
I will close this early. In 24 hours.
Target Market(s)
Rich mums
Industry/Entity Type
Shopping
Look and feel
Each slider illustrates characteristics of the customer's brand and the style your logo design should communicate.

```html
<!DOCTYPE html>
<html lang="en">
<head>
<meta charset="UTF-8">
<title>Velvet Nail Salon – Mother's Day Special</title>
<link href="https://fonts.googleapis.com/css2?family=Cinzel:wght@700&family=Montserrat:wght@300;400;800&family=Roboto+Condensed:wght@700&display=swap" rel="stylesheet">
<style>
  :root {
    --pink-light: #f2a9cf;
    --pink-mid: #e85ba4;
    --magenta: #d3136f;
    --magenta-deep: #b80c5e;
    --cream: #f7e6b5;
    --gold: #e9c77a;
    --white: #ffffff;
    --maroon: #5a0f1c;
    --red: #d0102a;
    --photo-skin: #eebfa9;
    --photo-blush: #f8e6ee;
    --photo-lilac: #d9a3dc;
    --photo-orchid: #c674c9;
  }
  * { margin: 0; padding: 0; box-sizing: border-box; }
  html, body { width: 847px; height: 1200px; overflow: hidden; background: var(--white); }
  .poster {
    position: relative;
    width: 847px;
    height: 1200px;
    overflow: hidden;
    font-family: "Montserrat", Arial, sans-serif;
  }
  .header {
    position: absolute;
    inset: 0 0 auto 0;
    height: 350px;
    background: linear-gradient(100deg, var(--pink-mid) 0%, #ee86bb 45%, var(--pink-light) 100%);
  }
  .brand-name {
    position: absolute;
    left: 150px;
    top: 112px;
    font-weight: 300;
    font-size: 104px;
    letter-spacing: 22px;
    color: var(--white);
    line-height: 1;
  }
  .brand-tagline {
    position: absolute;
    right: 121px;
    top: 230px;
    font-weight: 400;
    font-size: 38px;
    letter-spacing: 5px;
    color: var(--white);
    line-height: 1;
  }
  .offer-band {
    position: absolute;
    left: 0; right: 0;
    top: 350px;
    height: 142px;
    background: linear-gradient(90deg, var(--magenta-deep), var(--magenta) 60%, #e0338a);
  }
  .offer-title {
    position: absolute;
    left: 40px;
    top: 12px;
    font-family: "Cinzel", "Times New Roman", serif;
    font-weight: 700;
    font-size: 62px;
    color: var(--white);
    line-height: 1;
    white-space: nowrap;
    text-shadow: 0 0 10px rgba(255,255,255,0.5);
  }
  .offer-subtitle {
    position: absolute;
    left: 136px;
    top: 72px;
    font-family: "Montserrat", Arial, sans-serif;
    font-weight: 400;
    font-size: 64px;
    line-height: 1;
    white-space: nowrap;
    color: var(--cream);
    background: linear-gradient(180deg, #fff6dc, var(--gold));
    -webkit-background-clip: text;
    background-clip: text;
    -webkit-text-fill-color: transparent;
  }
  .hero-photo {
    position: absolute;
    left: 0; right: 0;
    top: 492px;
    height: 582px;
    background: linear-gradient(30deg,
      var(--photo-skin) 0%,
      #f3d2c4 30%,
      var(--photo-blush) 52%,
      var(--photo-lilac) 78%,
      var(--photo-orchid) 100%);
  }
  .voucher-burst {
    position: absolute;
    left: 570px;
    top: 274px;
    width: 280px;
    height: 280px;
  }
  .location-bar {
    position: absolute;
    left: 0; right: 0;
    bottom: 0;
    height: 126px;
    background: var(--magenta);
    display: flex;
    align-items: center;
    padding-left: 54px;
    gap: 20px;
  }
  .location-icon { width: 30px; height: 40px; flex: none; }
  .location-text {
    font-weight: 800;
    font-size: 48px;
    color: var(--white);
    letter-spacing: 1px;
    line-height: 1;
    white-space: nowrap;
  }
</style>
</head>
<body>
<main class="poster">
  <header class="header">
    <div class="brand-name">Velvet</div>
    <div class="brand-tagline">Nail Salon</div>
  </header>

  <section class="offer-band">
    <h1 class="offer-title">MOTHER’S DAY</h1>
    <h2 class="offer-subtitle">SPECIAL</h2>
  </section>

  <div class="hero-photo" role="img" aria-label="Photo of manicured hands with French tips resting on a soft white towel beside pink orchids and bottles of red and orange nail polish"></div>

  <svg class="voucher-burst" viewBox="-140 -140 280 280" aria-label="$10 gift voucher when you spend over $50">
    <polygon fill="#ffffff" stroke="#d3136f" stroke-width="5" stroke-linejoin="round"
      points="135,0 118.6,18.7 131.2,42.6 106.9,54.5 111.6,81.1 84.8,84.8 81.1,111.6 54.5,106.9 42.6,131.2 18.7,118.6 0,135 -18.7,118.6 -42.6,131.2 -54.5,106.9 -81.1,111.6 -84.8,84.8 -111.6,81.1 -106.9,54.5 -131.2,42.6 -118.6,18.7 -135,0 -118.6,-18.7 -131.2,-42.6 -106.9,-54.5 -111.6,-81.1 -84.8,-84.8 -81.1,-111.6 -54.5,-106.9 -42.6,-131.2 -18.7,-118.6 0,-135 18.7,-118.6 42.6,-131.2 54.5,-106.9 81.1,-111.6 84.8,-84.8 111.6,-81.1 106.9,-54.5 131.2,-42.6 118.6,-18.7"/>
    <polygon fill="none" stroke="#d3136f" stroke-width="1.5" transform="scale(0.91)"
      points="135,0 118.6,18.7 131.2,42.6 106.9,54.5 111.6,81.1 84.8,84.8 81.1,111.6 54.5,106.9 42.6,131.2 18.7,118.6 0,135 -18.7,118.6 -42.6,131.2 -54.5,106.9 -81.1,111.6 -84.8,84.8 -111.6,81.1 -106.9,54.5 -131.2,42.6 -118.6,18.7 -135,0 -118.6,-18.7 -131.2,-42.6 -106.9,-54.5 -111.6,-81.1 -84.8,-84.8 -81.1,-111.6 -54.5,-106.9 -42.6,-131.2 -18.7,-118.6 0,-135 18.7,-118.6 42.6,-131.2 54.5,-106.9 81.1,-111.6 84.8,-84.8 111.6,-81.1 106.9,-54.5 131.2,-42.6 118.6,-18.7"/>
    <g font-family="'Roboto Condensed', 'Arial Narrow', sans-serif" font-weight="700" text-anchor="middle">
      <text x="0" y="-14" font-size="98" fill="#5a0f1c">$10</text>
      <text x="0" y="20" font-size="26" fill="#d0102a">Gift voucher</text>
      <text x="0" y="54" font-size="26" fill="#d0102a">when you spend</text>
      <text x="0" y="92" font-size="34" fill="#d0102a">over $50</text>
    </g>
  </svg>

  <footer class="location-bar">
    <svg class="location-icon" viewBox="0 0 28 38" aria-hidden="true">
      <path d="M14 1C7 1 1.5 6.5 1.5 13.5 1.5 23 14 37 14 37S26.5 23 26.5 13.5C26.5 6.5 21 1 14 1Z" fill="#5a0f2c" stroke="#ffffff" stroke-width="2"/>
      <circle cx="14" cy="13.5" r="4.5" fill="#ffffff"/>
    </svg>
    <span class="location-text">Located near to Tallmart</span>
  </footer>
</main>
</body>
</html>
```